Wesbite design for Investment Firm

We want a basic (clean) website that follows the form, fonts and colors of our attachments. This is for a financial investment management firm, but we have a boutique (anti-Wall Street) approach. Site should have an Home Page (Logo up top - room for basic copy on bottom, Philosophy Page (room for Quarterly Letter attachment and basic copy, Performance Page (room for Performance Overview and Performance Analysis and basic copy), Team Page, Commentary Page and Contact

Reason: Some designers have asked for an extension. Again, please only use image of Train Station or Train Station Logo in design.

Target Market(s)

Small and mid-size financial advisors from across the country

Industry/Entity Type

Financial

Number of Pages Required

5+ page

Font styles to use
Other font styles liked:
• Palotino Linotype

Colors
3176b5
cfdeed
ffffff

Requirements
Must have
• Please refer to existing site www.qlvor.example. Of note, this is too complex / cluttered. We simply want Blur, Grey and White consistent with attachments. The copy is pretty good, but will be simplified (and no quotes)
Should not have
• No images other than train station logo and / or train station image

```html
<!DOCTYPE html>
<html lang="en">
<head>
<meta charset="utf-8">
<title>Harlow Street Investment Company</title>
<link href="https://fonts.googleapis.com/css2?family=Crimson+Text:wght@400;600&family=Montserrat:wght@600&family=Lato:ital@1&family=Arimo:ital@0;1&display=swap" rel="stylesheet">
<style>
:root{
  --brand:#3176b5;
  --brand-dark:#0b2d63;
  --navy:#062a5e;
  --footer:#3374b5;
  --tint:#cfdeed;
  --panel:#f0f0f0;
  --text:#5a5a5a;
  --white:#ffffff;
}
*{margin:0;padding:0;box-sizing:border-box}
html,body{width:1200px;height:2308px;overflow:hidden;background:var(--white)}
body{position:relative;font-family:'Arimo',Arial,sans-serif;color:var(--text)}
.serif{font-family:'Crimson Text','Palatino Linotype',serif}
.site-header{position:absolute;top:0;left:0;width:1200px;height:105px;text-align:center}
.brand-name{font-family:'Crimson Text','Palatino Linotype',serif;font-size:33px;font-weight:600;color:var(--brand-dark);font-variant:small-caps;letter-spacing:1.5px;line-height:105px}
.main-nav{position:absolute;top:105px;left:0;width:1200px;height:61px;background:var(--brand);display:flex;justify-content:center;align-items:center}
.main-nav a{color:var(--white);text-decoration:none;font-size:16px;padding:0 26px;border-right:2px solid rgba(11,45,99,.45)}
.main-nav a:last-of-type{border-right:none}
.main-nav svg{margin-left:26px}
.hero{position:absolute;top:166px;left:0;width:1200px;height:540px;overflow:hidden}
.hero-photo{position:absolute;inset:0;background:linear-gradient(180deg,#c7d3df 0%,#aebccb 35%,#8c9aaa 60%,#b9c3cd 100%)}
.hero-title{position:absolute;top:148px;width:100%;text-align:center;font-family:'Montserrat',sans-serif;font-weight:600;font-size:52px;color:var(--white);letter-spacing:-.5px}
.hero-sub{position:absolute;top:228px;width:100%;text-align:center;font-family:'Lato',sans-serif;font-style:italic;font-size:18px;color:var(--white)}
.hero-cta{position:absolute;top:280px;left:454px;width:292px;height:62px;background:var(--brand);border-radius:5px;color:var(--white);font-family:'Crimson Text',serif;font-size:22px;font-weight:600;letter-spacing:.5px;text-align:center;line-height:62px;box-shadow:0 4px 6px rgba(0,0,0,.3)}
.hero-arrow{position:absolute;top:212px}
.hero-edge{position:absolute;top:600px;left:0}
.dots{position:absolute;top:678px;left:549px;display:flex;gap:11px}
.dots span{width:17px;height:17px;border:2px solid var(--brand);border-radius:50%}
.dots span.on{background:var(--brand)}
.welcome{position:absolute;top:748px;left:150px;width:900px;text-align:center}
.welcome h1{font-family:'Crimson Text','Palatino Linotype',serif;font-weight:400;font-size:46px;color:var(--brand)}
.welcome p{margin-top:16px;font-size:14.5px;line-height:26.5px;color:#666}
.card{position:absolute;top:966px;width:334px;height:422px;background:var(--panel);text-align:center}
.card-head{height:57px;background:linear-gradient(180deg,#3f86c6,#2560a0);color:var(--white);font-family:'Crimson Text',serif;font-size:23px;line-height:57px;letter-spacing:.5px}
.card-img{margin:8px auto 0;width:320px;height:188px;border:1px solid #d0d0d0}
.card-text{margin-top:14px;font-size:14.5px;line-height:27px;color:#555;padding:0 14px}
.card-btn{position:absolute;bottom:0;left:83px;width:168px;height:57px;background:var(--brand);border-radius:6px 6px 0 0;color:var(--white);font-family:'Crimson Text',serif;font-size:21px;line-height:57px}
.login{position:absolute;top:1450px;left:77px;width:1046px;height:157px;background:var(--panel);border:1px solid #e0e0e0}
.login-tab{position:absolute;top:0;left:0}
.login-kicker{position:absolute;top:38px;left:18px;font-family:'Crimson Text',serif;font-size:17px;font-weight:600;color:var(--brand-dark)}
.login-title{position:absolute;top:58px;left:13px;font-family:'Crimson Text',serif;font-size:44px;color:var(--white)}
.field{position:absolute;top:52px;width:219px;height:57px;background:var(--white);font-size:14px;color:#666;line-height:57px;padding-left:16px}
.login-btn{position:absolute;top:51px;left:852px;width:188px;height:57px;background:var(--brand);border-radius:5px;color:var(--white);font-family:'Crimson Text',serif;font-size:24px;font-weight:600;text-align:center;line-height:57px}
.quote-mark{position:absolute;top:1678px;left:567px}
.quote-text{position:absolute;top:1768px;left:200px;width:800px;text-align:center;font-style:italic;font-size:17px;line-height:30px;color:#555}
.quote-by{position:absolute;top:1838px;width:1200px;text-align:center;font-family:'Crimson Text',serif;font-size:20px;font-weight:600;color:var(--brand)}
.quote-by::before{content:"";display:inline-block;width:24px;height:3px;background:var(--brand);vertical-align:middle;margin-right:12px}
.quote-arrow{position:absolute;top:1738px}
.site-footer{position:absolute;top:1905px;left:0;width:1200px;height:340px}
.footer-bg{position:absolute;top:0;left:0}
.footer-brand{position:absolute;top:111px;left:78px;font-family:'Crimson Text',serif;font-weight:600;font-size:18px;color:var(--white)}
.social{position:absolute;top:153px;left:128px;display:flex;gap:8px}
.social span{width:42px;height:40px;border:2px solid var(--white)}
.footer-col{position:absolute;top:76px;color:var(--white)}
.footer-col h3{font-family:'Crimson Text',serif;font-weight:600;font-size:18px;letter-spacing:.5px;margin-bottom:24px}
.footer-col li{list-style:none;font-size:14px;margin-bottom:16px}
.contact-row{display:flex;gap:14px;font-size:14px;line-height:23px;margin-bottom:16px}
.contact-row svg{flex:none;margin-top:2px}
.news p{width:250px;font-size:14px;line-height:22px}
.news-input{margin-top:8px;width:248px;height:46px;background:var(--white);color:#444;font-size:14px;line-height:46px;padding-left:10px}
.news-btn{margin-top:12px;width:166px;height:46px;border:2px solid var(--white);text-align:center;font-family:'Crimson Text',serif;font-size:21px;line-height:42px}
.copyright{position:absolute;top:2245px;left:0;width:1200px;height:63px;background:var(--navy);color:var(--white);font-size:14px;text-align:center;line-height:63px}
</style>
</head>
<body>
<header class="site-header"><div class="brand-name">Harlow Street Investment Company</div></header>

<nav class="main-nav">
  <a>HOME</a><a>PHILOSOPHY</a><a>PERFORMANCE</a><a>TEAM</a><a>LETTERS</a><a>COMMENTARY</a><a>CONTACT</a>
  <svg width="22" height="22" viewBox="0 0 22 22"><circle cx="9" cy="9" r="6.5" fill="none" stroke="#fff" stroke-width="3"/><line x1="14" y1="14" x2="20" y2="20" stroke="#fff" stroke-width="3.5" stroke-linecap="round"/></svg>
</nav>

<section class="hero">
  <div class="hero-photo" role="img" aria-label="Blurred office scene with business people meeting by bright windows"></div>
  <div class="hero-title">SEPARATELY MANAGED ACCOUNTS</div>
  <div class="hero-sub">The High Expectations of our Original Investors is a Key Contributor to our Value Driven Investment Philosophy.</div>
  <div class="hero-cta">CONTACT US TODAY</div>
  <svg class="hero-arrow" style="left:13px" width="52" height="52" viewBox="0 0 52 52"><circle cx="26" cy="26" r="24" fill="none" stroke="#0b2d63" stroke-width="2"/><path d="M30 15 L20 26 L30 37" fill="none" stroke="#0b2d63" stroke-width="2.5"/></svg>
  <svg class="hero-arrow" style="left:1135px" width="52" height="52" viewBox="0 0 52 52"><circle cx="26" cy="26" r="24" fill="none" stroke="#0b2d63" stroke-width="2"/><path d="M22 15 L32 26 L22 37" fill="none" stroke="#0b2d63" stroke-width="2.5"/></svg>
</section>
<svg class="hero-edge" width="1200" height="110" viewBox="0 0 1200 110">
  <path d="M0 62 Q300 90 540 92 L600 30 L660 92 Q900 90 1200 62 L1200 110 L0 110 Z" fill="#0b2d63"/>
  <path d="M0 72 Q300 98 540 100 L600 42 L660 100 Q900 98 1200 72 L1200 110 L0 110 Z" fill="#fff"/>
</svg>
<div class="dots"><span></span><span></span><span class="on"></span><span></span></div>

<section class="welcome">
  <h1>Welcome To Harlow Street Investment Company</h1>
  <p>We founded Harlow Street Investment Company in 1999, initially managing wealth from our family and friends in the town of Harlow Street. The high expectations of our original investors is a key contributor to our value driven investment philosophy. Based in Brookfield, TX, we manage assets for both individuals and institutions. Our investment methodology stresses absolute returns vs. relative performance, blending a combination of fundamental analysis, discipline and patience with the goal of preserving and compounding capital.</p>
</section>

<article class="card" style="left:77px">
  <div class="card-head">PHILOSOPHY</div>
  <div class="card-img" role="img" aria-label="Hand holding a small globe" style="background:linear-gradient(135deg,#f4f4f4,#e6dccf 55%,#9cc0d8)"></div>
  <div class="card-text">Buy at a Discount<br>Emphasis on Risk<br>Willingness to Hold Cash</div>
  <div class="card-btn">LEARN MORE</div>
</article>
<article class="card" style="left:433px">
  <div class="card-head">PERFORMANCE</div>
  <div class="card-img" role="img" aria-label="Pen and glasses resting on financial charts" style="background:linear-gradient(135deg,#4f6f95,#a9bdd3 50%,#dfe6ee)"></div>
  <div class="card-text">We believe trying to keep pace with the market in all environments promotes poor decisions and increases the probability.</div>
  <div class="card-btn">LEARN MORE</div>
</article>
<article class="card" style="left:789px">
  <div class="card-head">TEAM</div>
  <div class="card-img" role="img" aria-label="Team working together on the office floor" style="background:linear-gradient(135deg,#8a929a,#c9ccce 50%,#5d6469)"></div>
  <div class="card-text">Daniel P. Ashby<br>Thomas K. Wren<br>Martin L. Crowe</div>
  <div class="card-btn">LEARN MORE</div>
</article>

<section class="login">
  <svg class="login-tab" width="380" height="155" viewBox="0 0 380 155"><path d="M0 0 H344 L378 77 L344 155 H0 Z" fill="#0b2d63"/><path d="M0 0 H334 L368 77 L334 155 H0 Z" fill="#3176b5"/></svg>
  <div class="login-kicker">AUTHORIZATION</div>
  <div class="login-title">Our Commentary</div>
  <div class="field" style="left:394px">User_Name*</div>
  <div class="field" style="left:622px">Password*</div>
  <div class="login-btn">LOG IN</div>
</section>

<svg class="quote-mark" width="66" height="60" viewBox="0 0 66 60"><path d="M4 58 V34 Q4 8 28 2 L30 10 Q16 16 16 28 H28 V58 Z M38 58 V34 Q38 8 62 2 L64 10 Q50 16 50 28 H62 V58 Z" fill="#3176b5"/></svg>
<svg class="quote-arrow" style="left:77px" width="52" height="52" viewBox="0 0 52 52"><circle cx="26" cy="26" r="24" fill="none" stroke="#ccc" stroke-width="1.5"/><path d="M29 17 L21 26 L29 35" fill="none" stroke="#ccc" stroke-width="1.5"/></svg>
<svg class="quote-arrow" style="left:1071px" width="52" height="52" viewBox="0 0 52 52"><circle cx="26" cy="26" r="24" fill="none" stroke="#ccc" stroke-width="1.5"/><path d="M23 17 L31 26 L23 35" fill="none" stroke="#ccc" stroke-width="1.5"/></svg>
<p class="quote-text">"An investment operation is one which, upon thorough analysis, promises safety of principal and an adequate return. Operations not meeting these requirements are speculative."</p>
<div class="quote-by">Edwin Marlowe, The Patient Investor</div>

<footer class="site-footer">
  <svg class="footer-bg" width="1200" height="340" viewBox="0 0 1200 340">
    <path d="M0 0 Q600 36 1200 0 V340 H0 Z" fill="#0b2d63"/>
    <path d="M0 10 Q600 46 1200 10 V340 H0 Z" fill="#3374b5"/>
  </svg>
  <div class="footer-brand">Harlow Street Investment Company</div>
  <div class="social"><span></span><span></span><span></span></div>
  <div class="footer-col" style="left:345px">
    <h3>QUICK LINKS</h3>
    <ul><li>» Performance Overview</li><li>» Performance Analysis</li><li>» Verification Statement</li><li>» Harlow Street ADV Part 2</li></ul>
  </div>
  <div class="footer-col" style="left:608px">
    <h3>CONTACT US</h3>
    <div class="contact-row"><svg width="20" height="28" viewBox="0 0 20 28"><path d="M10 26 C4 17 2 13 2 9.5 A8 8 0 0 1 18 9.5 C18 13 16 17 10 26 Z" fill="none" stroke="#fff" stroke-width="1.6"/><circle cx="10" cy="9.5" r="3" fill="none" stroke="#fff" stroke-width="1.6"/></svg><span>Harlow Street Investment Company<br>2740 Linden Park Avenue,<br>Suite 1210 Brookfield,<br>TX 75000</span></div>
    <div class="contact-row"><svg width="20" height="20" viewBox="0 0 20 20"><path d="M3 2 L7 2 L9 7 L6.5 8.5 Q8 12 11.5 13.5 L13 11 L18 13 L18 17 Q10 19 5 13 Q1 8 3 2 Z" fill="none" stroke="#fff" stroke-width="1.5"/></svg><span>555.014.2290</span></div>
    <div class="contact-row"><svg width="20" height="16" viewBox="0 0 20 16"><rect x="1" y="2" width="18" height="12" fill="none" stroke="#fff" stroke-width="1.5"/><path d="M1 2 L10 9 L19 2" fill="none" stroke="#fff" stroke-width="1.5"/></svg><span>info@qlvor.example</span></div>
  </div>
  <div class="footer-col news" style="left:875px">
    <h3>NEWSLETTER</h3>
    <p>Would you like to receive exclusive access to articles, white papers and our regular monthly newsletter?</p>
    <div class="news-input">Enter Email Id</div>
    <div class="news-btn">SUBSCRIBE</div>
  </div>
</footer>
<div class="copyright">©Harlow Street Investment Company -2017 All rights reserved. | privecy policy</div>
</body>
</html>
```